Online business manager needs a website

I need a website designed and then coded. I am an online business manager serving a number of different industries providing administrative support to existing small businesses and helping solo practitioners get their new business up and running.

I didn't have a logo formally designed but have been using the attached avatar and wouldn't mind something that incorporated that.

The business doesn't have an official name, so I've just been using my name Lena Morvath, Online Business Manager or Lena Morvath, OBM. I've attached two documents that I have made previously for an example of content.

I would prefer the final site be in Wordpress.

Requirements
Must have
• A way to contact me, testimonials, list of services

```html
<!DOCTYPE html>
<html lang="en">
<head>
<meta charset="utf-8">
<title>Lena Morvath, OBM</title>
<link href="https://fonts.googleapis.com/css2?family=Poppins:wght@400;500;600;700;800&family=Lato:wght@400;700&family=IBM+Plex+Serif:wght@400&display=swap" rel="stylesheet">
<style>
:root{
  --purple:#4a1d8a;
  --purple-deep:#3b1570;
  --mint:#d7f1ee;
  --mint-btn:#d4f2ef;
  --teal:#22b8b0;
  --ink:#222222;
  --text:#444444;
  --footer:#272727;
  --white:#ffffff;
}
*{margin:0;padding:0;box-sizing:border-box}
html,body{width:1200px;height:3686px;overflow:hidden}
body{position:relative;background:var(--white);font-family:'Lato',sans-serif;color:var(--text)}
.abs{position:absolute}

/* header */
.logo{position:absolute;left:97px;top:30px;width:180px;text-align:center;line-height:1}
.logo-name{font-family:'Poppins',sans-serif;font-weight:700;font-size:25px;color:var(--ink);letter-spacing:.2px;white-space:nowrap}
.logo-sub{display:flex;align-items:center;justify-content:center;gap:14px;margin-top:4px;font-family:'Poppins',sans-serif;font-size:22px;color:var(--ink)}
.logo-sub::before,.logo-sub::after{content:"";width:42px;height:1.5px;background:var(--purple)}
.nav a{position:absolute;top:48px;font-size:15px;color:#444;text-decoration:none}
.btn-login{position:absolute;left:987px;top:29px;width:114px;height:55px;background:var(--mint-btn);border-radius:4px;font-family:'Poppins',sans-serif;font-weight:700;font-size:14px;color:var(--ink);display:flex;align-items:center;justify-content:center}

/* hero */
.hero{position:absolute;left:0;top:109px;width:1200px;height:688px;background:linear-gradient(100deg,#4d2690 0%,#6a43a6 45%,#7c58b4 70%,#5e3a9c 100%)}
.hero-photo{position:absolute;left:630px;top:0;width:570px;height:688px;background:linear-gradient(180deg,rgba(230,215,230,.25),rgba(180,160,200,.25))}
.hero-title{position:absolute;left:97px;top:122px;font-family:'Poppins',sans-serif;font-weight:700;font-size:98px;line-height:118px;color:var(--white)}
.btn-contact{position:absolute;left:99px;top:516px;width:113px;height:54px;border:2px solid #fff;border-radius:5px;color:#fff;font-family:'Poppins',sans-serif;font-weight:600;font-size:15px;display:flex;align-items:center;justify-content:center}
.dots{position:absolute;left:576px;top:622px;display:flex;gap:7px}
.dots span{width:12px;height:12px;border-radius:50%;background:#fff}
.dots span.off{background:transparent;border:2px solid #fff}

/* about */
.about-frame{left:76px;top:919px;width:290px;height:294px;border:3px solid var(--purple)}
.about-shadow{left:114px;top:968px;width:452px;height:456px;background:var(--mint)}
.about-photo{left:97px;top:951px;width:451px;height:456px;background:linear-gradient(135deg,#8a7f73,#c8a27c 50%,#9aa0a6)}
.h2{font-family:'Poppins',sans-serif;font-weight:700;color:var(--ink)}
.about-title{left:645px;top:943px;font-size:42px}
.rule{height:4px;width:75px;background:var(--purple)}
.about-text{left:645px;top:1050px;width:455px;font-family:'IBM Plex Serif',serif;font-size:14.5px;line-height:27px;color:#444}
.btn-more{left:645px;top:1337px;width:143px;height:54px;background:var(--mint-btn);border-radius:4px;font-family:'Poppins',sans-serif;font-weight:700;font-size:14px;color:var(--ink);display:flex;align-items:center;justify-content:center}

/* services */
.services{left:0;top:1556px;width:1200px;height:599px;background:var(--mint)}
.center-title{width:1200px;text-align:center;left:0;font-size:42px}
.card{position:absolute;top:1745px;width:229px;height:339px;background:#fff;border-radius:4px;box-shadow:0 2px 8px rgba(0,0,0,.06);text-align:center}
.card-img{margin:8px 8px 0;height:166px;border-radius:2px}
.card h3{font-family:'Poppins',sans-serif;font-weight:500;font-size:16.5px;line-height:27px;color:var(--ink);margin:20px 10px 10px}
.card p{font-size:13px;line-height:22.5px;color:#555;padding:0 12px}

/* testimonials */
.arrow{top:2505px}
.avatar{left:198px;top:2459px;width:122px;height:122px;border-radius:50%;border:6px solid var(--mint);background:linear-gradient(135deg,#c9b08a,#7d5a4a)}
.quote-text{left:380px;top:2450px;width:640px;font-family:'IBM Plex Serif',serif;font-size:14.5px;line-height:27px;color:#444}
.quote-name{left:380px;top:2548px;font-family:'Poppins',sans-serif;font-weight:500;font-size:17px;color:var(--ink)}

/* contact */
.contact{left:0;top:2693px;width:1200px;height:638px;background:linear-gradient(135deg,#e9e6f1,#dcd8e8 50%,#e6e2ee)}
.field{position:absolute;background:#fff;border-radius:4px;font-size:11.5px;color:#888;padding:24px 19px 0}
.btn-submit{left:529px;top:3173px;width:143px;height:54px;background:var(--purple);border-radius:3px;color:#fff;font-family:'Poppins',sans-serif;font-weight:700;font-size:14px;display:flex;align-items:center;justify-content:center}

/* footer */
.footer{left:0;top:3331px;width:1200px;height:355px;background:var(--footer);color:#fff}
.footer .logo-name,.footer .logo-sub{color:#fff}
.footer .logo-sub::before,.footer .logo-sub::after{background:#ccc}
.fhead{position:absolute;top:3399px;font-family:'Poppins',sans-serif;font-weight:500;font-size:18px;color:#fff}
.flinks{left:413px;top:3440px;font-size:15.5px;line-height:26.5px;color:#fff}
.finfo{font-size:14px;line-height:21px;color:#fff}
.social{position:absolute;top:3521px;width:36px;height:36px;border-radius:50%;background:var(--teal)}
.copy{left:0;top:3625px;width:1200px;text-align:center;font-size:14px;color:#fff}
</style>
</head>
<body>

<header>
  <div class="logo">
    <div class="logo-name">LENA MORVATH</div>
    <div class="logo-sub">OBM</div>
  </div>
  <nav class="nav">
    <a style="left:392px">Home</a>
    <a style="left:478px">About Me</a>
    <a style="left:588px">About Services</a>
    <a style="left:735px">Testimoials</a>
    <a style="left:858px">Contact Us</a>
  </nav>
  <div class="btn-login">LOG IN</div>
</header>

<section class="hero" role="img" aria-label="Office background in purple tones with a smiling woman holding a tablet">
  <div class="hero-photo"></div>
  <h1 class="hero-title">Online<br>Business<br>Manager</h1>
  <div class="btn-contact">CONTACT</div>
  <div class="dots"><span></span><span class="off"></span><span></span></div>
</section>

<section>
  <div class="abs about-frame"></div>
  <div class="abs about-shadow"></div>
  <div class="abs about-photo" role="img" aria-label="Portrait photo of the business manager outdoors on a city street"></div>
  <h2 class="abs h2 about-title">About Me</h2>
  <div class="abs rule" style="left:645px;top:1009px"></div>
  <p class="abs about-text">Hi! I'm so excited that you have chosen to explore my portfolio. Helping businesses achieve their goals is my passion, and I'm thrilled that with my assistance you will have more time for your own passion project. I thrive while working independently, which means you can be confident when leaving tasks for me. The type of work that lights me up is anything involving organization and/or spreadsheets. You need data analyzed that includes multiple nested if formulas? You have an overwhelming amount of email to sort through and appointments to book? I'm your gal!</p>
  <div class="abs btn-more">MORE ABOUT</div>
</section>

<section>
  <div class="abs services"></div>
  <h2 class="abs h2 center-title" style="top:1617px">Our Services</h2>
  <div class="abs rule" style="left:562px;top:1686px"></div>
  <div class="card" style="left:99px">
    <div class="card-img" role="img" aria-label="Laptop on a desk with a calendar" style="background:linear-gradient(135deg,#cfd3da,#8a8f99)"></div>
    <h3>Virtual Assistance</h3>
    <p>Calendar Management Email Management Light Graphic Design Data Entry</p>
  </div>
  <div class="card" style="left:358px">
    <div class="card-img" role="img" aria-label="Typed note on paper beside a plant" style="background:linear-gradient(90deg,#5c6a3e,#dcdcd8 45%)"></div>
    <h3>Social Media &amp; Content Management</h3>
    <p>Content Repurposing Graphics Creation Audiogram Creation Search Engine Optimization</p>
  </div>
  <div class="card" style="left:615px">
    <div class="card-img" role="img" aria-label="Desk with calculator, notebook and laptop" style="background:linear-gradient(135deg,#9fd3df,#e4eef0)"></div>
    <h3>Finance Management</h3>
    <p>Create Invoices Track Receivables Analyze Expenses Year Over Year Analytics</p>
  </div>
  <div class="card" style="left:874px">
    <div class="card-img" role="img" aria-label="Woman at a desk in front of a wall of sticky notes" style="background:linear-gradient(135deg,#d9a3a8,#e3e0a0 55%,#7b8c92)"></div>
    <h3>Business Management</h3>
    <p>Creation of Operating Procedures Review of Website Strategy Reporting and Analytics Project Managemen</p>
  </div>
</section>

<section>
  <h2 class="abs h2 center-title" style="top:2275px">Client Love</h2>
  <div class="abs rule" style="left:562px;top:2344px"></div>
  <svg class="abs arrow" style="left:99px" width="20" width="20" height="30" viewBox="0 0 20 30"><path d="M15 3 L4 15 L15 27" fill="none" stroke="#222" stroke-width="3"/></svg>
  <svg class="abs arrow" style="left:1086px" width="20" height="30" viewBox="0 0 20 30"><path d="M5 3 L16 15 L5 27" fill="none" stroke="#222" stroke-width="3"/></svg>
  <div class="abs avatar" role="img" aria-label="Client headshot"></div>
  <svg class="abs" style="left:323px;top:2420px" width="42" height="28" viewBox="0 0 42 28" fill="#4a1d8a"><circle cx="10" cy="10" r="9"/><path d="M2 12 Q4 24 14 27 Q7 20 9 14Z"/><circle cx="31" cy="10" r="9"/><path d="M23 12 Q25 24 35 27 Q28 20 30 14Z"/></svg>
  <svg class="abs" style="left:955px;top:2548px" width="42" height="28" viewBox="0 0 42 28" fill="#4a1d8a"><circle cx="11" cy="18" r="9"/><path d="M40 16 Q38 4 28 1 Q35 8 33 14Z"/><circle cx="32" cy="18" r="9"/><path d="M19 16 Q17 4 7 1 Q14 8 12 14Z"/></svg>
  <p class="abs quote-text">When it became apparent that a project would take more time than I had, Lena stepped up to take on the required research. She was thorough and timely; able to meet a last-minute 12-hour deadline. I would highly recommend Lena to assist with your next project.</p>
  <div class="abs quote-name">Dana R. Whitfield, Northgate Roofing</div>
</section>

<section>
  <div class="abs contact" role="img" aria-label="Faded photo of two people shaking hands in an office"></div>
  <h2 class="abs h2 center-title" style="top:2776px">Contact Us</h2>
  <div class="abs rule" style="left:562px;top:2845px"></div>
  <div class="field" style="left:253px;top:2899px;width:336px;height:54px">Name</div>
  <div class="field" style="left:611px;top:2899px;width:336px;height:54px">Phone Number</div>
  <div class="field" style="left:253px;top:2979px;width:336px;height:54px">Email</div>
  <div class="field" style="left:611px;top:2979px;width:336px;height:54px">Subject</div>
  <div class="field" style="left:253px;top:3056px;width:694px;height:84px;padding-top:22px">Email</div>
  <div class="abs btn-submit">SUBMIT</div>
</section>

<footer>
  <div class="abs footer"></div>
  <div class="logo" style="left:99px;top:3428px;width:196px">
    <div class="logo-name" style="font-size:27px">LENA MORVATH</div>
    <div class="logo-sub" style="font-size:24px">OBM</div>
  </div>
  <div class="social" style="left:98px"></div>
  <div class="social" style="left:148px"></div>

  <div class="fhead" style="left:413px">QUICK LINKS</div>
  <div class="abs flinks">Home<br>About Me<br>About Services<br>Testimoials<br>Contact Us</div>

  <div class="fhead" style="left:641px">CONTACT US</div>
  <svg class="abs" style="left:641px;top:3444px" width="14" height="19" viewBox="0 0 14 19"><path d="M7 0C3 0 0 3 0 7c0 5 7 12 7 12s7-7 7-12c0-4-3-7-7-7z" fill="#fff"/><circle cx="7" cy="7" r="2.6" fill="#272727"/></svg>
  <div class="abs finfo" style="left:669px;top:3442px;width:170px">Lorem ipsum dolor sit amet, consectetur</div>
  <svg class="abs" style="left:641px;top:3493px" width="16" height="16" viewBox="0 0 24 24"><path d="M6.6 10.8c1.4 2.8 3.8 5.1 6.6 6.6l2.2-2.2c.3-.3.7-.4 1-.2 1.1.4 2.3.6 3.6.6.6 0 1 .4 1 1V20c0 .6-.4 1-1 1C10.6 21 3 13.4 3 4c0-.6.4-1 1-1h3.5c.6 0 1 .4 1 1 0 1.3.2 2.5.6 3.6.1.3 0 .7-.2 1z" fill="#fff"/></svg>
  <div class="abs finfo" style="left:670px;top:3490px">555.214.0198</div>
  <svg class="abs" style="left:641px;top:3533px" width="16" height="12" viewBox="0 0 16 12"><rect width="16" height="12" rx="1" fill="#fff"/><path d="M1 1l7 6 7-6" fill="none" stroke="#272727" stroke-width="1.4"/></svg>
  <div class="abs finfo" style="left:669px;top:3528px">lena.morvath@example.com</div>

  <div class="fhead" style="left:907px">NEWSLETTER</div>
  <div class="abs" style="left:907px;top:3446px;width:196px;height:35px;background:#fff;border-radius:4px;font-size:12.5px;color:#888;padding:9px 12px">Ener email</div>
  <div class="abs" style="left:1056px;top:3446px;width:47px;height:35px;background:var(--teal);border-radius:0 4px 4px 0;display:flex;align-items:center;justify-content:center">
    <svg width="14" height="10" viewBox="0 0 16 12"><rect width="16" height="12" rx="1" fill="#fff"/><path d="M1 1l7 6 7-6" fill="none" stroke="#22b8b0" stroke-width="1.4"/></svg>
  </div>

  <div class="abs copy">©Copyrights 2023 Lena Morvath &nbsp;|&nbsp; All Rights Reserved</div>
</footer>

</body>
</html>
```